Honey Label

We are seeking a label design for our range of Honey products, which form part of our extensive gourmet condiment collection. Our store is a destination for food tourism, offering a wide array of handcrafted jams, marmalades, sauces, aiolis, and more. The label needs to align visually with our existing range but also distinctly represent honey.
Label Purpose & Use:
To be used across a wide variety of honey products including single origin and flavoured varieties (e.g. Orange & Cinnamon Honey, Rose Honey, Raspberry Honey, Spiced Chai Honey, Iron back, Shoalhaven).
Labels will be overprinted with specific product names, so the design must allow for clear, flexible space for this.
Design Objectives:
Complement existing condiment range in style and tone.
Visually communicate honey as the primary product (bee, hive, flora, golden hues etc.).
Include traditional design cues with a touch of cute, fun, and whimsical charm. Design must maintain a gourmet, high-quality feel while still appealing to gift shoppers and food lovers.
Consider tourism appeal – the product should feel ‘special’ or gift-worthy.
Please include all detail as per 250g label 2025 (first attachment).
Photo of honey in the 375g jar attached.
Label size options include:
- Same as 205g label attached.
Or
- custom size. Maximum 120mm x 120mm (including label backing) as it must run through our thermal printer. Please include seal tab up onto lid.

```html
<!DOCTYPE html>
<html lang="en">
<head>
<meta charset="UTF-8">
<title>Rose Honey Label</title>
<link href="https://fonts.googleapis.com/css2?family=IM+Fell+English&family=Roboto+Slab:wght@700&family=Roboto+Condensed:wght@500&family=Montserrat:wght@500&display=swap" rel="stylesheet">
<style>
  :root {
    --paper: #ffffff;
    --cream: #fbf3cf;
    --cream-deep: #f6e9b4;
    --honey: #f4a32e;
    --honey-deep: #ec8f1f;
    --maroon: #87271f;
    --maroon-dark: #6e1c16;
    --ink: #1e1a17;
    --bee-tone: #a9654e;
  }
  * { margin: 0; padding: 0; box-sizing: border-box; }
  html, body { width: 1200px; height: 1200px; overflow: hidden; background: var(--paper); }
  .canvas { position: relative; width: 1200px; height: 1200px; }

  .seal-tab {
    position: absolute; left: 520px; top: 70px; width: 160px; height: 380px;
    background: linear-gradient(90deg, var(--honey) 0 32%, var(--maroon) 32% 68%, var(--honey) 68% 100%);
  }

  .label {
    position: absolute; left: 100px; top: 440px; width: 1000px; height: 540px;
    background: var(--cream);
  }
  .band {
    position: absolute; left: 0; width: 100%;
    background: linear-gradient(180deg, var(--honey), var(--honey-deep));
    border-top: 8px solid var(--maroon);
    border-bottom: 8px solid var(--maroon);
    display: flex; align-items: center; justify-content: space-between;
    padding: 0 18px;
  }
  .band--top { top: 0; height: 110px; align-items: flex-end; padding-bottom: 14px; }
  .band--bottom { bottom: 0; height: 105px; justify-content: center; align-items: flex-start; padding-top: 14px; border-bottom: none; }

  .tagline {
    font-family: "Montserrat", sans-serif; font-weight: 500;
    font-size: 13px; letter-spacing: 3px; color: var(--maroon);
    display: flex; align-items: center; gap: 8px;
  }
  .dot { width: 9px; height: 9px; border-radius: 50%; background: var(--maroon); display: inline-block; }

  .origin {
    font-family: "Roboto Condensed", sans-serif; font-weight: 500;
    font-size: 22px; color: var(--maroon); display: flex; align-items: center; gap: 12px;
  }

  .brand {
    position: absolute; left: 0; width: 100%; top: 128px;
    display: flex; justify-content: center; align-items: center; gap: 16px;
  }
  .brand-mark { width: 22px; height: 22px; background: var(--maroon); }
  .brand-name {
    font-family: "Roboto Slab", serif; font-weight: 700;
    font-size: 30px; letter-spacing: 9px; color: var(--maroon); text-transform: uppercase;
  }

  .product-name {
    position: absolute; left: 0; width: 100%; top: 220px; text-align: center;
    font-family: "IM Fell English", serif; font-size: 120px; line-height: 1;
    color: var(--ink);
  }

  .bee {
    position: absolute; width: 95px; height: 120px; border-radius: 48% 48% 45% 45%;
    background: radial-gradient(ellipse at center, var(--bee-tone) 0 30%, var(--cream-deep) 70%);
  }
  .bee--left { left: 10px; top: 150px; }
  .bee--right { right: 10px; top: 260px; }
</style>
</head>
<body>
<div class="canvas">
  <div class="seal-tab" role="img" aria-label="Seal tab with honeycomb pattern and maroon centre stripe"></div>

  <section class="label">
    <div class="band band--top" role="img" aria-label="Honeycomb pattern band">
      <span class="tagline">QUALITY <span class="dot"></span><span class="dot"></span><span class="dot"></span><span class="dot"></span><span class="dot"></span></span>
      <span class="tagline"><span class="dot"></span><span class="dot"></span><span class="dot"></span><span class="dot"></span><span class="dot"></span> HANDMADE</span>
    </div>

    <div class="brand">
      <span class="brand-mark"></span>
      <span class="brand-name">Hollowbrook Treats</span>
    </div>

    <div class="bee bee--left" role="img" aria-label="Engraved bee illustration"></div>
    <h1 class="product-name">Rose Honey</h1>
    <div class="bee bee--right" role="img" aria-label="Engraved bee illustration"></div>

    <div class="band band--bottom" role="img" aria-label="Honeycomb pattern band">
      <span class="origin"><span class="dot"></span><span class="dot"></span><span class="dot"></span> Proudly Australian owned and made <span class="dot"></span><span class="dot"></span><span class="dot"></span></span>
    </div>
  </section>
</div>
</body>
</html>
```